Pebble Tracks - explore habits of productive people

Pebble Tracks is a social place around habits and productivity

The full brief below:

https://notes.brimwellpad.net/page/d/7Qx-RtVmPLa93KwBz-H-cNmq2YeTsRfvUdGkHpXwaB/view?mode=shared

Colors

Designer to choose colors to be used in the design.

Requirements
Must have
• - a feed page to display habits
• - a habit page to add a habit
• / clean, no cluttered design, lots of white space
• / inspired by material design or other design system
Nice to have
• - user page

```html
<!DOCTYPE html>
<html lang="en">
<head>
<meta charset="utf-8">
<title>Pebble Tracks – Habit Feed</title>
<link href="https://fonts.googleapis.com/css2?family=Lato:wght@400;700;900&display=swap" rel="stylesheet">
<style>
  :root{
    --teal:#1ba68b;
    --teal-light:#2bd37f;
    --page-bg:#efefef;
    --white:#ffffff;
    --ink:#1d1d1d;
    --ink-soft:#444444;
    --muted:#7a7a7a;
    --line:#e3e3e3;
    --btn-border:#8a8a8a;
    --comment-bg:#f7f3f4;
    --comment-border:#e2dcdd;
    --avatar-a:#6b5a4e;
    --avatar-b:#8c6f5f;
    --avatar-c:#3e3a3a;
  }
  *{box-sizing:border-box;margin:0;padding:0}
  html,body{width:1200px;height:2195px;overflow:hidden}
  body{font-family:'Lato',sans-serif;background:var(--page-bg);color:var(--ink);position:relative}

  .topbar{position:absolute;left:0;top:0;width:1200px;height:61px;
    background:linear-gradient(90deg,var(--teal) 0%,var(--teal-light) 12%,var(--teal) 30%,var(--teal) 100%);
    display:flex;align-items:center;padding:0 20px}
  .brand{font-weight:900;font-size:28px;color:var(--white);letter-spacing:.5px;text-transform:uppercase}
  .topbar-right{margin-left:auto;display:flex;align-items:center;gap:10px;color:var(--white);font-size:14px}
  .greeting b{font-weight:700}
  .caret{width:10px;height:10px;margin-left:2px}
  .top-avatar{width:24px;height:24px;border-radius:50%;background:var(--avatar-a);margin:0 18px 0 12px}
  .add-habit{display:flex;align-items:center;gap:8px;height:32px;padding:0 14px;border:2px solid var(--white);
    color:var(--white);font-weight:900;font-size:13px;text-transform:uppercase;letter-spacing:.3px}

  .sidebar{position:absolute;left:0;top:61px;width:224px;height:2084px;background:var(--white)}
  .sidebar-user{height:66px;display:flex;align-items:center;padding-left:21px;gap:16px;font-size:14px;border-bottom:1px solid var(--line)}
  .sidebar-user .avatar{width:28px;height:28px;border-radius:50%;background:var(--avatar-c)}
  .nav{list-style:none}
  .nav li{height:44px;display:flex;align-items:center;padding-left:27px;gap:18px;font-size:15px;color:var(--ink-soft);border-bottom:1px solid var(--line)}
  .nav li svg{width:18px;height:18px;flex:none}
  .nav li.active{background:var(--teal);color:var(--white);font-weight:700;border-bottom-color:var(--teal)}

  .main{position:absolute;left:263px;top:0;width:902px}
  .page-title{position:absolute;top:94px;left:0;font-weight:900;font-size:29px;letter-spacing:.5px;color:var(--ink)}
  .feed{position:absolute;top:155px;left:0;width:902px}
  .card{background:var(--white);padding:25px 33px 32px 37px;margin-bottom:16px;box-shadow:0 1px 2px rgba(0,0,0,.04)}
  .author{display:flex;align-items:center;gap:12px;margin-left:-4px}
  .author .avatar{width:46px;height:46px;border-radius:50%}
  .author-name{font-size:15px;color:var(--ink)}
  .author-time{font-size:12px;color:var(--muted);margin-top:2px}
  .post-text{margin-top:22px;font-size:14.6px;line-height:19px;color:var(--ink);max-width:780px}
  .actions{display:flex;align-items:center;margin-top:20px}
  .btn{display:flex;align-items:center;gap:6px;height:26px;padding:0 9px;border:1px solid var(--btn-border);font-size:12px;color:var(--ink-soft);margin-right:10px;background:var(--white)}
  .btn svg{width:13px;height:13px}
  .stats{margin-left:auto;display:flex;gap:16px;color:var(--teal);font-size:12px}
  .stat{display:flex;align-items:center;gap:5px}
  .stat svg{width:13px;height:13px}
  .comment-box{margin-top:25px;height:45px;border:1px solid var(--comment-border);background:var(--comment-bg);
    display:flex;align-items:center;padding:0 12px 0 19px;font-size:12.5px;color:var(--ink-soft)}
  .comment-box .tools{margin-left:auto;display:flex;gap:10px}
  .comment-box svg{width:18px;height:18px}

  .view-more{position:absolute;left:363px;top:2049px;width:116px;height:35px;background:var(--teal);color:var(--white);
    font-weight:900;font-size:12.5px;display:flex;align-items:center;justify-content:center;text-transform:uppercase;letter-spacing:.3px}

  .footer{position:absolute;left:0;top:2145px;width:1200px;height:50px;background:var(--teal);color:var(--white);
    font-size:12px;display:flex;align-items:center;justify-content:center}
</style>
</head>
<body>

<header class="topbar">
  <div class="brand">Pebble Tracks</div>
  <div class="topbar-right">
    <span class="greeting">Hello, <b>Dorian</b></span>
    <svg class="caret" viewBox="0 0 10 10"><path d="M2 3.5 5 6.5 8 3.5" fill="none" stroke="#fff" stroke-width="1.3"/></svg>
    <div class="top-avatar" role="img" aria-label="Profile photo of Dorian"></div>
    <div class="add-habit">
      <svg width="12" height="12" viewBox="0 0 12 12"><path d="M6 1v10M1 6h10" stroke="#fff" stroke-width="2.4"/></svg>
      Add Habit
    </div>
  </div>
</header>

<aside class="sidebar">
  <div class="sidebar-user">
    <div class="avatar" role="img" aria-label="Profile photo of Dorian"></div>
    <span>Dorian</span>
  </div>
  <ul class="nav">
    <li class="active"><svg viewBox="0 0 18 18" fill="none" stroke="currentColor" stroke-width="1.3"><rect x="3" y="2" width="12" height="14"/><path d="M6 6h6M6 9h6M6 12h4"/></svg>Habit</li>
    <li><svg viewBox="0 0 18 18" fill="none" stroke="currentColor" stroke-width="1.2"><circle cx="5" cy="5" r="2"/><circle cx="13" cy="5" r="2"/><circle cx="9" cy="7" r="2"/><path d="M2 15v-4a3 3 0 0 1 6 0M10 15v-4a3 3 0 0 1 6 0M6 16v-3a3 3 0 0 1 6 0v3"/></svg>Groups</li>
    <li><svg viewBox="0 0 18 18" fill="none" stroke="currentColor" stroke-width="1.2"><rect x="2" y="3" width="14" height="13"/><path d="M2 7h14M6 1v4M12 1v4M5 10h2M8 10h2M11 10h2M5 13h2M8 13h2"/></svg>Planner</li>
    <li><svg viewBox="0 0 18 18" fill="none" stroke="currentColor" stroke-width="1.2"><path d="M4 2h8l3 3v11H4z"/><path d="M6 7h6M6 10h6M6 13h4"/></svg>Documents</li>
    <li><svg viewBox="0 0 18 18" fill="currentColor"><rect x="2" y="8" width="3" height="8"/><rect x="7" y="3" width="3" height="13"/><rect x="12" y="10" width="3" height="6"/></svg>Polls</li>
    <li><svg viewBox="0 0 18 18" fill="none" stroke="currentColor" stroke-width="1.2"><path d="M2 8c0-3 3-5 6-5s6 2 6 5-3 5-6 5l-4 2 1-3c-2-1-3-2-3-4z"/><path d="M15 10c1 1 1 3 0 4l1 2-3-1"/></svg>Quiz</li>
    <li><svg viewBox="0 0 18 18" fill="none" stroke="currentColor" stroke-width="1.2"><circle cx="9" cy="6" r="3.5"/><path d="M2.5 16c0-3.5 3-6 6.5-6s6.5 2.5 6.5 6z"/></svg>Profile</li>
    <li><svg viewBox="0 0 18 18" fill="none" stroke="currentColor" stroke-width="1.2"><circle cx="9" cy="9" r="2.5"/><path d="M9 1.5v2.5M9 14v2.5M1.5 9h2.5M14 9h2.5M3.7 3.7l1.8 1.8M12.5 12.5l1.8 1.8M3.7 14.3l1.8-1.8M12.5 5.5l1.8-1.8"/><circle cx="9" cy="9" r="5.2"/></svg>Settings</li>
  </ul>
</aside>

<main class="main">
  <h1 class="page-title">HABIT</h1>

  <section class="feed">
    <article class="card">
      <div class="author">
        <div class="avatar" style="background:var(--avatar-a)" role="img" aria-label="Profile photo of Tobin Ferrow"></div>
        <div><div class="author-name">Tobin Ferrow</div><div class="author-time">3 hours ago</div></div>
      </div>
      <p class="post-text">After I pour my cup of coffee each morning, I will meditate for one minute. ed ut perspiciatis unde omnis iste natus error sit voluptatem accusantium doloremque laudantium, totam rem aperiam.</p>
      <div class="actions">
        <span class="btn"><svg viewBox="0 0 14 14" fill="none" stroke="currentColor" stroke-width="1"><path d="M1 6h3v7H1zM4 6l3-5c1 0 2 1 1.5 2.5L8 5h4c1 0 1.5 1 1 2l-1.5 5c-.2.7-.8 1-1.5 1H4"/></svg>Like</span>
        <span class="btn"><svg viewBox="0 0 14 14" fill="none" stroke="currentColor" stroke-width="1"><path d="M8 2l5 4-5 4V8C4 8 2 9 1 12c0-4 2-7 7-7z"/></svg>Share</span>
        <div class="stats">
          <span class="stat"><svg viewBox="0 0 14 14" fill="none" stroke="currentColor" stroke-width="1"><path d="M1 6h3v7H1zM4 6l3-5c1 0 2 1 1.5 2.5L8 5h4c1 0 1.5 1 1 2l-1.5 5c-.2.7-.8 1-1.5 1H4"/></svg>20 Likes</span>
          <span class="stat"><svg viewBox="0 0 14 14" fill="none" stroke="currentColor" stroke-width="1"><path d="M1 6c0-2 2-4 5-4s5 2 5 4-2 4-5 4l-3 2 .5-2.5C2 8.5 1 7.5 1 6z"/><path d="M12 7.5c1 1 1 2.5 0 3.5l.5 2-2.5-1"/></svg>85 Comments</span>
        </div>
      </div>
      <div class="comment-box">Write a Comment....
        <div class="tools">
          <svg viewBox="0 0 18 18" fill="none" stroke="#8a8a8a" stroke-width="1"><circle cx="9" cy="9" r="7"/><circle cx="6.5" cy="7.5" r=".6" fill="#8a8a8a"/><circle cx="11.5" cy="7.5" r=".6" fill="#8a8a8a"/><path d="M6 11c1.5 1.5 4.5 1.5 6 0"/></svg>
          <svg viewBox="0 0 18 18" fill="none" stroke="#8a8a8a" stroke-width="1"><path d="M2 5h3l1.5-2h5L13 5h3v10H2z"/><circle cx="9" cy="10" r="3"/></svg>
        </div>
      </div>
    </article>

    <article class="card">
      <div class="author">
        <div class="avatar" style="background:var(--avatar-b)" role="img" aria-label="Profile photo of Elton Marsh"></div>
        <div><div class="author-name">Elton Marsh</div><div class="author-time">05 December 2018</div></div>
      </div>
      <p class="post-text">After I take off my work shoes, I will immediately change into my workout clothes. Sed ut perspiciatis unde omnis iste natus error sit voluptatem accusantium doloremque laudantium, totam rem aperiam, eaque ipsa quae ab illo inventore veritatis et quasi architecto beatae vitae dicta.</p>
      <div class="actions">
        <span class="btn"><svg viewBox="0 0 14 14" fill="none" stroke="currentColor" stroke-width="1"><path d="M1 6h3v7H1zM4 6l3-5c1 0 2 1 1.5 2.5L8 5h4c1 0 1.5 1 1 2l-1.5 5c-.2.7-.8 1-1.5 1H4"/></svg>Like</span>
        <span class="btn"><svg viewBox="0 0 14 14" fill="none" stroke="currentColor" stroke-width="1"><path d="M8 2l5 4-5 4V8C4 8 2 9 1 12c0-4 2-7 7-7z"/></svg>Share</span>
        <div class="stats">
          <span class="stat"><svg viewBox="0 0 14 14" fill="none" stroke="currentColor" stroke-width="1"><path d="M1 6h3v7H1zM4 6l3-5c1 0 2 1 1.5 2.5L8 5h4c1 0 1.5 1 1 2l-1.5 5c-.2.7-.8 1-1.5 1H4"/></svg>20 Likes</span>
          <span class="stat"><svg viewBox="0 0 14 14" fill="none" stroke="currentColor" stroke-width="1"><path d="M1 6c0-2 2-4 5-4s5 2 5 4-2 4-5 4l-3 2 .5-2.5C2 8.5 1 7.5 1 6z"/><path d="M12 7.5c1 1 1 2.5 0 3.5l.5 2-2.5-1"/></svg>85 Comments</span>
        </div>
      </div>
      <div class="comment-box">Write a Comment....
        <div class="tools">
          <svg viewBox="0 0 18 18" fill="none" stroke="#8a8a8a" stroke-width="1"><circle cx="9" cy="9" r="7"/><circle cx="6.5" cy="7.5" r=".6" fill="#8a8a8a"/><circle cx="11.5" cy="7.5" r=".6" fill="#8a8a8a"/><path d="M6 11c1.5 1.5 4.5 1.5 6 0"/></svg>
          <svg viewBox="0 0 18 18" fill="none" stroke="#8a8a8a" stroke-width="1"><path d="M2 5h3l1.5-2h5L13 5h3v10H2z"/><circle cx="9" cy="10" r="3"/></svg>
        </div>
      </div>
    </article>

    <article class="card">
      <div class="author">
        <div class="avatar" style="background:var(--avatar-b)" role="img" aria-label="Profile photo of Wren"></div>
        <div><div class="author-name">Wren</div><div class="author-time">3 hours ago</div></div>
      </div>
      <p class="post-text">After I sit down to dinner, I will say one thing I’m grateful for that happened today. "Lorem ipsum dolor sit amet, consectetur adipiscing elit, sed do eiusmod tempor incididunt ut labore et dolore magna aliqua. Ut enim ad minim veniam</p>
      <div class="actions">
        <span class="btn"><svg viewBox="0 0 14 14" fill="none" stroke="currentColor" stroke-width="1"><path d="M1 6h3v7H1zM4 6l3-5c1 0 2 1 1.5 2.5L8 5h4c1 0 1.5 1 1 2l-1.5 5c-.2.7-.8 1-1.5 1H4"/></svg>Like</span>
        <span class="btn"><svg viewBox="0 0 14 14" fill="none" stroke="currentColor" stroke-width="1"><path d="M8 2l5 4-5 4V8C4 8 2 9 1 12c0-4 2-7 7-7z"/></svg>Share</span>
        <div class="stats">
          <span class="stat"><svg viewBox="0 0 14 14" fill="none" stroke="currentColor" stroke-width="1"><path d="M1 6h3v7H1zM4 6l3-5c1 0 2 1 1.5 2.5L8 5h4c1 0 1.5 1 1 2l-1.5 5c-.2.7-.8 1-1.5 1H4"/></svg>20 Likes</span>
          <span class="stat"><svg viewBox="0 0 14 14" fill="none" stroke="currentColor" stroke-width="1"><path d="M1 6c0-2 2-4 5-4s5 2 5 4-2 4-5 4l-3 2 .5-2.5C2 8.5 1 7.5 1 6z"/><path d="M12 7.5c1 1 1 2.5 0 3.5l.5 2-2.5-1"/></svg>85 Comments</span>
        </div>
      </div>
      <div class="comment-box">Write a Comment....
        <div class="tools">
          <svg viewBox="0 0 18 18" fill="none" stroke="#8a8a8a" stroke-width="1"><circle cx="9" cy="9" r="7"/><circle cx="6.5" cy="7.5" r=".6" fill="#8a8a8a"/><circle cx="11.5" cy="7.5" r=".6" fill="#8a8a8a"/><path d="M6 11c1.5 1.5 4.5 1.5 6 0"/></svg>
          <svg viewBox="0 0 18 18" fill="none" stroke="#8a8a8a" stroke-width="1"><path d="M2 5h3l1.5-2h5L13 5h3v10H2z"/><circle cx="9" cy="10" r="3"/></svg>
        </div>
      </div>
    </article>

    <article class="card">
      <div class="author">
        <div class="avatar" style="background:var(--avatar-c)" role="img" aria-label="Profile photo of Owen Hale"></div>
        <div><div class="author-name">Owen Hale</div><div class="author-time">05 December 2018</div></div>
      </div>
      <p class="post-text">After I put on my running shoes, I will text a friend or family member where I am running and how long it will take. At vero eos et accusamus et iusto odio dignissimos ducimus qui blanditiis praesentium voluptatum deleniti atque corrupti quos dolores et quas molestias excepturi sint occaecati cupiditate non provident, similique sunt in culpa qui officia deserunt mollitia animi, id est laborum et dolorum</p>
      <div class="actions">
        <span class="btn"><svg viewBox="0 0 14 14" fill="none" stroke="currentColor" stroke-width="1"><path d="M1 6h3v7H1zM4 6l3-5c1 0 2 1 1.5 2.5L8 5h4c1 0 1.5 1 1 2l-1.5 5c-.2.7-.8 1-1.5 1H4"/></svg>Like</span>
        <span class="btn"><svg viewBox="0 0 14 14" fill="none" stroke="currentColor" stroke-width="1"><path d="M8 2l5 4-5 4V8C4 8 2 9 1 12c0-4 2-7 7-7z"/></svg>Share</span>
        <div class="stats">
          <span class="stat"><svg viewBox="0 0 14 14" fill="none" stroke="currentColor" stroke-width="1"><path d="M1 6h3v7H1zM4 6l3-5c1 0 2 1 1.5 2.5L8 5h4c1 0 1.5 1 1 2l-1.5 5c-.2.7-.8 1-1.5 1H4"/></svg>20 Likes</span>
          <span class="stat"><svg viewBox="0 0 14 14" fill="none" stroke="currentColor" stroke-width="1"><path d="M1 6c0-2 2-4 5-4s5 2 5 4-2 4-5 4l-3 2 .5-2.5C2 8.5 1 7.5 1 6z"/><path d="M12 7.5c1 1 1 2.5 0 3.5l.5 2-2.5-1"/></svg>85 Comments</span>
        </div>
      </div>
      <div class="comment-box">Write a Comment....
        <div class="tools">
          <svg viewBox="0 0 18 18" fill="none" stroke="#8a8a8a" stroke-width="1"><circle cx="9" cy="9" r="7"/><circle cx="6.5" cy="7.5" r=".6" fill="#8a8a8a"/><circle cx="11.5" cy="7.5" r=".6" fill="#8a8a8a"/><path d="M6 11c1.5 1.5 4.5 1.5 6 0"/></svg>
          <svg viewBox="0 0 18 18" fill="none" stroke="#8a8a8a" stroke-width="1"><path d="M2 5h3l1.5-2h5L13 5h3v10H2z"/><circle cx="9" cy="10" r="3"/></svg>
        </div>
      </div>
    </article>

    <article class="card">
      <div class="author">
        <div class="avatar" style="background:var(--avatar-c)" role="img" aria-label="Profile photo of Elton Marsh"></div>
        <div><div class="author-name">Elton Marsh</div><div class="author-time">05 December 2018</div></div>
      </div>
      <p class="post-text">After I get into bed at night, I will give my partner a kiss.. Sed ut perspiciatis unde omnis iste natus error sit voluptatem accusantium doloremque laudantium, totam rem aperiam, eaque ipsa quae ab illo inventore veritatis et quasi architecto beatae vitae dicta.</p>
      <div class="actions">
        <span class="btn"><svg viewBox="0 0 14 14" fill="none" stroke="currentColor" stroke-width="1"><path d="M1 6h3v7H1zM4 6l3-5c1 0 2 1 1.5 2.5L8 5h4c1 0 1.5 1 1 2l-1.5 5c-.2.7-.8 1-1.5 1H4"/></svg>Like</span>
        <span class="btn"><svg viewBox="0 0 14 14" fill="none" stroke="currentColor" stroke-width="1"><path d="M8 2l5 4-5 4V8C4 8 2 9 1 12c0-4 2-7 7-7z"/></svg>Share</span>
        <div class="stats">
          <span class="stat"><svg viewBox="0 0 14 14" fill="none" stroke="currentColor" stroke-width="1"><path d="M1 6h3v7H1zM4 6l3-5c1 0 2 1 1.5 2.5L8 5h4c1 0 1.5 1 1 2l-1.5 5c-.2.7-.8 1-1.5 1H4"/></svg>20 Likes</span>
          <span class="stat"><svg viewBox="0 0 14 14" fill="none" stroke="currentColor" stroke-width="1"><path d="M1 6c0-2 2-4 5-4s5 2 5 4-2 4-5 4l-3 2 .5-2.5C2 8.5 1 7.5 1 6z"/><path d="M12 7.5c1 1 1 2.5 0 3.5l.5 2-2.5-1"/></svg>85 Comments</span>
        </div>
      </div>
      <div class="comment-box">Write a Comment....
        <div class="tools">
          <svg viewBox="0 0 18 18" fill="none" stroke="#8a8a8a" stroke-width="1"><circle cx="9" cy="9" r="7"/><circle cx="6.5" cy="7.5" r=".6" fill="#8a8a8a"/><circle cx="11.5" cy="7.5" r=".6" fill="#8a8a8a"/><path d="M6 11c1.5 1.5 4.5 1.5 6 0"/></svg>
          <svg viewBox="0 0 18 18" fill="none" stroke="#8a8a8a" stroke-width="1"><path d="M2 5h3l1.5-2h5L13 5h3v10H2z"/><circle cx="9" cy="10" r="3"/></svg>
        </div>
      </div>
    </article>

    <article class="card">
      <div class="author">
        <div class="avatar" style="background:var(--avatar-a)" role="img" aria-label="Profile photo of Tobin Ferrow"></div>
        <div><div class="author-name">Tobin Ferrow</div><div class="author-time">3 hours ago</div></div>
      </div>
      <p class="post-text">After I sit down to dinner, I will say one thing I’m grateful for that happened today. "Lorem ipsum dolor sit amet, consectetur adipiscing elit, sed do eiusmod tempor incididunt ut labore et dolore magna aliqua. Ut enim ad minim veniam</p>
      <div class="actions">
        <span class="btn"><svg viewBox="0 0 14 14" fill="none" stroke="currentColor" stroke-width="1"><path d="M1 6h3v7H1zM4 6l3-5c1 0 2 1 1.5 2.5L8 5h4c1 0 1.5 1 1 2l-1.5 5c-.2.7-.8 1-1.5 1H4"/></svg>Like</span>
        <span class="btn"><svg viewBox="0 0 14 14" fill="none" stroke="currentColor" stroke-width="1"><path d="M8 2l5 4-5 4V8C4 8 2 9 1 12c0-4 2-7 7-7z"/></svg>Share</span>
        <div class="stats">
          <span class="stat"><svg viewBox="0 0 14 14" fill="none" stroke="currentColor" stroke-width="1"><path d="M1 6h3v7H1zM4 6l3-5c1 0 2 1 1.5 2.5L8 5h4c1 0 1.5 1 1 2l-1.5 5c-.2.7-.8 1-1.5 1H4"/></svg>20 Likes</span>
          <span class="stat"><svg viewBox="0 0 14 14" fill="none" stroke="currentColor" stroke-width="1"><path d="M1 6c0-2 2-4 5-4s5 2 5 4-2 4-5 4l-3 2 .5-2.5C2 8.5 1 7.5 1 6z"/><path d="M12 7.5c1 1 1 2.5 0 3.5l.5 2-2.5-1"/></svg>85 Comments</span>
        </div>
      </div>
      <div class="comment-box">Write a Comment....
        <div class="tools">
          <svg viewBox="0 0 18 18" fill="none" stroke="#8a8a8a" stroke-width="1"><circle cx="9" cy="9" r="7"/><circle cx="6.5" cy="7.5" r=".6" fill="#8a8a8a"/><circle cx="11.5" cy="7.5" r=".6" fill="#8a8a8a"/><path d="M6 11c1.5 1.5 4.5 1.5 6 0"/></svg>
          <svg viewBox="0 0 18 18" fill="none" stroke="#8a8a8a" stroke-width="1"><path d="M2 5h3l1.5-2h5L13 5h3v10H2z"/><circle cx="9" cy="10" r="3"/></svg>
        </div>
      </div>
    </article>
  </section>

  <div class="view-more">View More</div>
</main>

<footer class="footer">Terms and Conditions &nbsp;|&nbsp; Copyrights @ 2018 All Rights Reserved</footer>

</body>
</html>
```